A4 4-sided brochure - medical specialist

A4 sized, 4 sided brochure, glossy. I am a medical specialist (urologist) and need a brochure to hand out to GPs. I will write all text and will send photos. I have attached an example of the kind of thing I was thinking of. My website is https://www.harbourpointclinic.com.au/
There are three of us in a group but the brochure is just for me.
It is to give to GPs and not direct to patients, so should tell the GPs why they should refer to me.
Target Market(s)
Medical
Industry/Entity Type
medicine - surgery - urology
Requirements
Must have
- I have uploaded an outline of the layout with files that are listed on the outline - please load them up as indicated and submit your designs
Should not have
- Claims that I am the best

```html
<!DOCTYPE html>
<html lang="en">
<head>
<meta charset="utf-8">
<title>Harbour Point Clinic – Urology Brochure</title>
<link rel="stylesheet" href="https://fonts.googleapis.com/css2?family=Roboto:wght@400;500;700;900&display=swap">
<style>
:root{
  --bg:#e6e7e9;
  --paper:#ffffff;
  --navy:#175a93;
  --navy-dark:#124c7e;
  --accent:#1b8bd6;
  --teal:#46b5d1;
  --ink:#2b2f33;
  --ink-soft:#4a4f55;
  --frame:#c9ccd1;
  --art-skin:#e9b49b;
  --art-red:#c7473d;
}
*{box-sizing:border-box;margin:0;padding:0}
html,body{width:1200px;height:1070px;overflow:hidden;background:var(--bg);font-family:'Roboto',Arial,sans-serif;color:var(--ink)}
.spread{position:absolute;width:720px;height:510px;background:var(--paper);box-shadow:0 2px 10px rgba(0,0,0,.12);overflow:hidden}
.spread--outside{left:40px;top:20px}
.spread--inside{left:440px;top:545px}
.abs{position:absolute}

.band{background:var(--navy);background-image:repeating-linear-gradient(125deg,rgba(255,255,255,.035) 0 40px,rgba(0,0,0,.04) 40px 80px)}

h3.sec{font-size:8px;font-weight:500;color:var(--accent);margin-bottom:2px}
ul.ticks{list-style:none}
ul.ticks li{position:relative;padding-left:8px;font-size:5.3px;line-height:8.45px;color:var(--ink)}
ul.ticks li::before{content:"";position:absolute;left:0;top:2px;width:4.5px;height:4.5px;border-radius:50%;background:var(--accent)}
ul.ticks li::after{content:"";position:absolute;left:1.4px;top:3.1px;width:1.4px;height:.9px;border-left:.7px solid #fff;border-bottom:.7px solid #fff;transform:rotate(-45deg)}
ul.ticks--white li{color:#fff;line-height:7.5px;font-size:5.6px;margin-bottom:3.5px;text-align:justify}
ul.ticks--white li::before{background:#5fb2e8}

.art{border:1px solid var(--frame);background:#fff;padding:4px}
.art__fill{width:100%;height:100%}

.brand{display:flex;align-items:center;gap:6px;font-weight:500;color:var(--ink-soft)}
.brand__dot{border-radius:50%;background:var(--accent);flex:none}

/* outside spread */
.back{left:0;top:0;width:336px;height:510px}
.contact{left:22px;top:423px}
.contact h4{font-size:9px;font-weight:700;color:var(--ink);margin-bottom:4px;letter-spacing:.2px}
.contact p{font-size:6.4px;line-height:9.6px;color:var(--ink);display:flex;align-items:flex-start;gap:4px}
.ico{width:7px;height:7px;flex:none;margin-top:1.3px}
.cover-photo{left:398px;top:127px;width:322px;height:262px;border:3px solid #fff;border-right:none;background:linear-gradient(90deg,#3a2a22,#6e5040 45%,#3b2b22);box-shadow:0 0 0 1px rgba(255,255,255,.6)}
.tagline{left:507px;top:401px;width:190px;font-size:9.4px;line-height:12.3px;font-weight:700;color:#3b4046;text-align:justify}
.urlbar{left:353px;top:478px;width:367px;height:17px;background:var(--teal);clip-path:polygon(10px 0,100% 0,100% 100%,0 100%);color:#fff;font-size:7.6px;line-height:17px;text-align:right;padding-right:22px}

/* inside spread */
.values{left:0;top:0;width:175px;height:510px}
.ops-photo{left:22px;top:23px;width:315px;height:158px;border:2px solid #fff;background:linear-gradient(180deg,#d9dbdc,#b8bdc2 55%,#3d5f95 80%,#2f4f86)}
.values-text{left:21px;top:190px;width:136px;color:#fff}
.values-text h3{font-size:10.5px;font-weight:700;color:#5fb8ee;margin-bottom:3px}
.values-text p{font-size:6.3px;line-height:8.8px;text-align:justify;margin-bottom:8px}
.gps{left:194px;top:190px;width:150px}
.gps h2{font-size:9.8px;font-weight:700;color:var(--ink);margin-bottom:1px}
.gps h3.sec{margin-top:3px;margin-bottom:1px;font-size:7.8px}
.gps ul.ticks li{font-size:5.6px;line-height:9.7px;font-weight:500}
.info{left:380px;top:19px;width:330px}
.info h2{font-size:9.4px;font-weight:900;color:var(--ink);letter-spacing:.1px;margin-bottom:3px}
.info .sec{font-size:7.8px}
.cols{display:flex;gap:8px}
</style>
</head>
<body>

<!-- OUTSIDE SPREAD: back panel, band, cover -->
<section class="spread spread--outside">
  <div class="back abs">
    <div class="abs" style="left:22px;top:19px;width:180px">
      <h3 class="sec">The Bladder</h3>
      <ul class="ticks">
        <li>Bladder augmentation surgery</li>
        <li>Bladder biopsy</li>
        <li>Bladder chemotherapy</li>
        <li>Bladder immunotherapy</li>
        <li>Bladder neck incision</li>
        <li>Pharmaceutical neurotoxin Injection into Bladder</li>
        <li>Continent urinary diversion</li>
        <li>Cystectomy and ileal conduit</li>
        <li>Cystectomy and orthotopic bladder replacement</li>
        <li>Cystodistension</li>
        <li>Cystolitholapaxy (removal of bladder stones)</li>
        <li>Cystolithotomy (open removal of bladder stones)</li>
        <li>Cystoscopy under local anaesthetic</li>
        <li>Cystoscopy under general anaesthetic</li>
        <li>DMSO Bladder Instillation</li>
        <li>Examination under anaesthesia</li>
        <li>Ileal conduit alone</li>
        <li>Insertion of suprapubic catheter</li>
        <li>Repair of vesicovaginal fistula</li>
        <li>Transurethral resection of bladder tumour</li>
        <li>Urodynamics</li>
      </ul>
    </div>
    <div class="abs" style="left:22px;top:215px;width:172px">
      <h3 class="sec">The Urethra</h3>
      <ul class="ticks">
        <li style="text-align:justify">Insertion of artificial urinary sphincter for stress urinary incontinence</li>
        <li>Insertion of urethral stent</li>
        <li>Meatal dilatation</li>
        <li>Optical laser urethrotomy</li>
        <li>Optical urethrotomy</li>
        <li>Sling procedures for male stress urinary incontinence – Adjustable</li>
        <li>Sling procedures for male stress urinary incontinence – Fixed</li>
        <li>Urethral dilatation</li>
        <li>Urethroplasty</li>
        <li>Urethroscopy</li>
        <li>Intermittent self catheterisation for males</li>
        <li>Intermittent self catheterisation for females</li>
      </ul>
    </div>
    <div class="abs" style="left:22px;top:352px;width:180px">
      <h3 class="sec">Other Complex Major Surgery</h3>
      <ul class="ticks">
        <li>Retroperitoneal lymph node dissection for testis cancer</li>
        <li>Retroperitoneal sarcoma surgery</li>
        <li>Ureterolysis</li>
      </ul>
    </div>

    <div class="art abs" style="left:196px;top:22px;width:132px;height:187px">
      <div class="art__fill" role="img" aria-label="Anatomical cross-section illustrations of the male and female pelvis and bladder" style="background:linear-gradient(180deg,#f6e3d8,var(--art-skin) 30%,#f3ddd0 50%,var(--art-skin) 75%,#f6e3d8)"></div>
    </div>
    <div class="art abs" style="left:196px;top:218px;width:132px;height:186px">
      <div class="art__fill" role="img" aria-label="Anatomical cross-section illustrations of the male and female urethra" style="background:linear-gradient(180deg,#f6e3d8,var(--art-skin) 30%,#f3ddd0 50%,var(--art-skin) 75%,#f6e3d8)"></div>
    </div>

    <div class="contact abs">
      <h4>CONTACT US</h4>
      <p><svg class="ico" viewBox="0 0 10 10"><circle cx="5" cy="5" r="4.6" fill="none" stroke="#1b8bd6" stroke-width="1"/><path d="M2.6 5.2 5 3 7.4 5.2M3.4 4.7V7h3.2V4.7" fill="none" stroke="#1b8bd6" stroke-width=".9"/></svg><span>Bayview Medical Suites, 12 Harbour Street,<br>Port Adams, SA 5099</span></p>
      <p><svg class="ico" viewBox="0 0 10 10"><circle cx="5" cy="5" r="4.6" fill="none" stroke="#1b8bd6" stroke-width="1"/><path d="M3.3 2.8c.3-.3.7-.3.9 0l.5.8c.1.3 0 .5-.2.7l-.3.3c.3.7.8 1.2 1.5 1.5l.3-.3c.2-.2.4-.3.7-.2l.8.5c.3.2.3.6 0 .9-.5.5-1.3.6-2 .2A6 6 0 0 1 3.1 4.8c-.4-.7-.3-1.5.2-2Z" fill="#1b8bd6"/></svg><span>8555 0142</span>
        <svg class="ico" viewBox="0 0 10 10" style="margin-left:6px"><circle cx="5" cy="5" r="4.6" fill="none" stroke="#1b8bd6" stroke-width="1"/><rect x="3.6" y="2.4" width="2.8" height="5.2" rx=".5" fill="none" stroke="#1b8bd6" stroke-width=".8"/></svg><span>0400 555 271</span></p>
      <p><svg class="ico" viewBox="0 0 10 10"><circle cx="5" cy="5" r="4.6" fill="none" stroke="#1b8bd6" stroke-width="1"/><rect x="2.7" y="3.6" width="4.6" height="3" fill="none" stroke="#1b8bd6" stroke-width=".8"/><rect x="3.5" y="2.5" width="3" height="1.2" fill="#1b8bd6"/></svg><span>8555 0199</span>
        <svg class="ico" viewBox="0 0 10 10" style="margin-left:6px"><circle cx="5" cy="5" r="4.6" fill="none" stroke="#1b8bd6" stroke-width="1"/><rect x="2.7" y="3.3" width="4.6" height="3.4" fill="none" stroke="#1b8bd6" stroke-width=".8"/><path d="M2.7 3.3 5 5.2l2.3-1.9" fill="none" stroke="#1b8bd6" stroke-width=".8"/></svg><span>info@bayviewsuites.com.au</span></p>
      <p><svg class="ico" viewBox="0 0 10 10"><circle cx="5" cy="5" r="4.6" fill="none" stroke="#1b8bd6" stroke-width="1"/><circle cx="5" cy="5" r="2.5" fill="none" stroke="#1b8bd6" stroke-width=".7"/><path d="M2.5 5h5M5 2.5v5" stroke="#1b8bd6" stroke-width=".6"/></svg><span>www.harbourpointclinic.com.au</span></p>
    </div>

    <div class="brand abs" style="left:200px;top:448px;font-size:11px">
      <span class="brand__dot" style="width:14px;height:14px"></span>Harbour Point Clinic
    </div>
  </div>

  <div class="band abs" style="left:336px;top:0;width:149px;height:510px"></div>
  <div class="band abs" style="left:485px;top:127px;width:235px;height:262px"></div>

  <div class="brand abs" style="left:505px;top:62px;font-size:14px">
    <span class="brand__dot" style="width:18px;height:18px"></span>Harbour Point Clinic
  </div>

  <div class="cover-photo abs" role="img" aria-label="Portrait photograph of three urologists in dark suits standing in front of timber panelling"></div>

  <p class="tagline abs">A complete urology service is offered for your patients regardless of insurance status, with rapid access and a friendly, professional &amp; evidence-based approach to care.</p>
  <div class="urlbar abs">www.harbourpointclinic.com.au</div>
</section>

<!-- INSIDE SPREAD: values, GP panel, procedures -->
<section class="spread spread--inside">
  <div class="values band abs"></div>
  <div class="ops-photo abs" role="img" aria-label="Photograph of three surgeons in blue scrubs beside a robotic surgical system in an operating theatre"></div>

  <div class="values-text abs">
    <h3>OUR VALUES</h3>
    <p style="font-size:6.9px;line-height:9.2px">We are aware that you have many choices in who provides your health care, and we appreciate that you are putting your trust in us.</p>
    <p style="font-size:6.9px;line-height:9.2px">Our approach to your care governs everything we do for you, and it consists of the following elements:</p>
    <ul class="ticks ticks--white">
      <li>We want you to feel comfortable with all of our staff, and we will make every effort to make your visits as stress free as possible.</li>
      <li>We recognise that each patient is an individual with different needs.</li>
      <li>We want to work in partnership with you so that you are actively involved in decisions about your care. Our role is to give you options for treatment and advice, and for you to make the decision that you feel most comfortable with, with our guidance if necessary.</li>
      <li>We believe that the more information you have about your condition and options for treatment, the better decisions we will make together as a partnership, and the better the outcomes for you. To this end, we have a large amount of information on the practice website, and encourage you to use this.</li>
      <li>Your Family Doctor/referring practitioner is central to all of your care. After each consultation or treatment, we will ensure that he/she is sent communication on the same day.</li>
      <li>If there is anything that we could do better, please let us know. Our practice is Your practice.</li>
    </ul>
  </div>

  <div class="gps abs">
    <h2>FOR GPS</h2>
    <h3 class="sec">Make a Referral</h3>
    <ul class="ticks"><li>GP Referral Form</li></ul>
    <h3 class="sec">Help with Urology Problems</h3>
    <ul class="ticks">
      <li>Epididymal Cysts</li><li>Epididymitis</li><li>Erectile Dysfunction</li><li>Haematospermia</li>
      <li>Hydrocoele</li><li>Incontinence in Women</li><li>Inflammation of the Foreskin / Balanitis</li>
      <li>Microscopic Haematuria</li><li>Nocturnal Incontinence</li><li>Paraphimosis/Foreskin Stuck Behind Glans</li>
      <li>Penile Curvature</li><li>Premature Ejaculation</li><li>Priapism</li><li>Retrograde Ejaculation</li>
      <li>Screening for Prostate Cancer with PSA</li><li>Sterile Pyuria</li><li>Testosterone Deficiency / Hypogonadism</li>
      <li>Tight Foreskin/Phimosis</li><li>Urethral Catheter Problems</li><li>Urinary Tract Infection in Men</li>
      <li>Urinary Tract Infection in Women</li><li>Varicocoele (Adults)</li>
    </ul>
    <h3 class="sec">Urological Procedures</h3>
    <ul class="ticks"><li>Urological Procedures</li></ul>
    <h3 class="sec">Contact Harbour Point Clinic</h3>
    <ul class="ticks"><li>Contact Harbour Point Clinic</li></ul>
  </div>

  <div class="info abs">
    <h2>INFORMATION ON UROLOGICAL PROCEDURES AND INVESTIGATIONS</h2>
    <h3 class="sec">The Prostate</h3>
    <ul class="ticks" style="margin-bottom:5px">
      <li>Active surveillance for prostate cancer</li>
      <li>Photoselective Laser Treatment for BPH</li>
      <li>LDR brachytherapy for prostate cancer</li>
      <li>HDR brachytherapy for prostate cancer</li>
      <li>Open retropubic prostatectomy for benign prostatic hyperplasia (BPH)</li>
      <li>Prostatic Artery Embolisation for BPH</li>
      <li>Radical prostatectomy/robotic radical prostatectomy</li>
      <li>Transperineal grid prostate biopsy</li>
      <li>Transrectal ultrasound-guided biopsy of the prostate</li>
      <li>Transurethral resection of the prostate</li>
    </ul>
    <h3 class="sec">The Penis</h3>
    <ul class="ticks" style="margin-bottom:5px">
      <li>Circumcision</li>
      <li>Foreskin sparing surgery for phimosis including frenuloplasty</li>
      <li>Glans penis excision and reconstruction for cancer</li>
      <li>Partial penile amputation &amp; reconstruction for cancer</li>
      <li>Penile prosthesis for erectile dysfunction</li>
      <li>Peyronie's disease operations</li>
      <li>Preputioplasty, dorsal and ventral slit</li>
      <li>Priapism - operations</li>
      <li>Treatments for impotence</li>
      <li>Treatment of penile warts</li>
      <li>Total penile amputation and perineal urethrostomy</li>
    </ul>
    <h3 class="sec">The Scrotum and Testes</h3>
    <ul class="ticks" style="margin-bottom:5px">
      <li>Epididymal cyst excision</li>
      <li>Excision of sebaceous cysts of the scrotum</li>
      <li>Hydrocele repair</li>
      <li>Insertion of testicular prosthesis</li>
      <li>Orchidectomy for benign problems <span style="font-size:4px">(removal of testicle for benign disease)</span></li>
      <li>Orchidectomy for testis cancer (removal of testicle for cancer)</li>
      <li>Laparoscopic orchidectomy for undescended testis</li>
      <li>Testicular fixation (Orchidopexy)</li>
      <li>Varicocoele surgery</li>
      <li>Vasectomy</li>
      <li>Vasectomy reversal</li>
    </ul>
    <h3 class="sec">The Kidney and Ureter</h3>
    <div class="cols">
      <ul class="ticks">
        <li>Active surveillance for small renal tumours</li>
        <li>Insertion and removal of ureteric stents</li>
        <li>Insertion of metallic ureteric stent</li>
        <li>Laparoscopic de-roofing of renal cysts</li>
        <li>Laparoscopic nephrectomy</li>
        <li>Laparoscopic pyeloplasty</li>
        <li>Laparoscopic nephroureterectomy</li>
        <li>Laser surgery for kidney/ureteric stones</li>
        <li>Open nephroureterectomy</li>
        <li>Percutaneous Nephrolithotomy (PCNL)</li>
        <li>Reimplantation of ureter into bladder</li>
        <li>Robotic kidney surgery</li>
        <li>Ureteroscopy (semi-rigid)</li>
        <li>Ureterorenoscopy (flexible)</li>
      </ul>
      <ul class="ticks">
        <li>Robotic pyeloplasty</li>
        <li>Nephrostomy</li>
        <li>Open pyeloplasty</li>
        <li>Open nephrectomy</li>
        <li>Partial nephrectomy</li>
        <li>Treatment of VUR</li>
      </ul>
    </div>
  </div>

  <div class="art abs" style="left:573px;top:36px;width:124px;height:89px">
    <div class="art__fill" role="img" aria-label="Medical illustration of prostate cancer stages" style="background:radial-gradient(circle at 30% 45%,#e08a6e,#f3d8cc 45%,#fff 70%),#fff"></div>
  </div>
  <div class="art abs" style="left:573px;top:137px;width:124px;height:98px">
    <div class="art__fill" role="img" aria-label="Medical illustration of penile cross-section anatomy" style="background:radial-gradient(ellipse at 50% 40%,#f5e3b8,#fbf1e0 45%,#fff 70%)"></div>
  </div>
  <div class="art abs" style="left:573px;top:252px;width:124px;height:98px">
    <div class="art__fill" role="img" aria-label="Medical illustration of the scrotum and testes with vas deferens" style="background:radial-gradient(ellipse at 50% 70%,#e7a36f,#f6dcc7 45%,#fff 72%)"></div>
  </div>
  <div class="art abs" style="left:573px;top:363px;width:124px;height:123px">
    <div class="art__fill" role="img" aria-label="Medical illustration of kidney cross-section and ureter" style="background:radial-gradient(ellipse at 45% 45%,#d9674f,#f1c1aa 45%,#fff 72%)"></div>
  </div>
</section>

</body>
</html>
```